KLV Plant Services

We are a heavy diesel mechanical business with additional air con certificates, remapping engine rebuilt

Contact Information for Business Card

Company Name, Director Name, Managing Director, Contact details, email and website

Font styles to use
Serif
Script

```html
<!DOCTYPE html>
<html lang="en">
<head>
<meta charset="utf-8">
<title>KLV Plant Services – Business Card</title>
<link href="https://fonts.googleapis.com/css2?family=Noto+Serif:wght@400;700&family=Dancing+Script:wght@500&display=swap" rel="stylesheet">
<style>
  :root {
    --navy: #2b2c7a;
    --text: #2e2e33;
    --card: #ffffff;
    --backdrop: #3a3a3a;
    --art-light: #e4e4e8;
    --art-dark: #b4b4bb;
  }
  * { margin: 0; padding: 0; box-sizing: border-box; }
  html, body {
    width: 1200px; height: 780px; overflow: hidden;
    background: var(--backdrop);
    font-family: "Noto Serif", Georgia, serif;
  }
  .canvas {
    position: relative; width: 1200px; height: 780px;
    display: flex; align-items: center; justify-content: center; gap: 40px;
  }
  .card {
    position: relative; width: 540px; height: 309px;
    background: var(--card); border-radius: 22px; overflow: hidden;
  }
  /* Contact side */
  .brand {
    position: absolute; left: 28px; top: 24px;
    display: flex; align-items: center; gap: 10px;
    color: var(--navy); font-weight: 700; font-size: 22px; line-height: 1;
  }
  .brand-dot {
    width: 14px; height: 14px; border-radius: 50%; background: var(--navy); flex: none;
  }
  .person {
    position: absolute; left: 0; top: 74px; padding-left: 28px;
  }
  .person-bar {
    position: absolute; left: 0; top: 2px; width: 12px; height: 44px; background: var(--navy);
  }
  .person-name {
    color: var(--navy); font-weight: 700; font-size: 19px; letter-spacing: 0.5px; line-height: 1.2;
  }
  .person-role {
    color: var(--navy); font-family: "Dancing Script", cursive; font-weight: 500;
    font-size: 19px; line-height: 1.1; margin-top: 1px;
  }
  .address {
    position: absolute; left: 28px; top: 138px;
    color: var(--text); font-size: 13px; line-height: 1.45;
  }
  .contacts {
    position: absolute; left: 28px; top: 190px; list-style: none;
    color: var(--text); font-size: 13px; line-height: 1.55;
  }
  .contacts li { display: flex; align-items: center; gap: 7px; }
  .contacts svg { width: 12px; height: 12px; fill: var(--navy); flex: none; }
  .machine-art {
    position: absolute; right: 28px; bottom: 28px; width: 240px; height: 190px;
    background: linear-gradient(140deg, var(--art-light), var(--art-dark));
    border-radius: 14px;
  }
  /* Logo side */
  .card-back { display: flex; align-items: center; justify-content: center; }
  .back-brand {
    display: flex; align-items: center; gap: 16px;
    color: var(--navy); font-weight: 700; font-size: 36px;
  }
  .back-brand .brand-dot { width: 22px; height: 22px; }
</style>
</head>
<body>
<main class="canvas">
  <section class="card card-front" aria-label="Business card contact side">
    <div class="brand"><span class="brand-dot"></span>KLV Plant Services</div>
    <div class="person">
      <span class="person-bar"></span>
      <div class="person-name">DANIEL HARPER</div>
      <div class="person-role">Managing Director</div>
    </div>
    <div class="address">Your address, City<br>State, Zip 1234</div>
    <ul class="contacts">
      <li><svg viewBox="0 0 24 24"><path d="M6.6 10.8a15.1 15.1 0 0 0 6.6 6.6l2.2-2.2c.3-.3.7-.4 1-.2 1.1.4 2.3.6 3.6.6.6 0 1 .4 1 1V20c0 .6-.4 1-1 1A17 17 0 0 1 3 4c0-.6.4-1 1-1h3.5c.6 0 1 .4 1 1 0 1.3.2 2.5.6 3.6.1.3 0 .7-.2 1z"/></svg>123 456 789</li>
      <li><svg viewBox="0 0 24 24"><path d="M2 5h20v14H2zm2 2v.5l8 5 8-5V7l-8 5z"/></svg>info@yourgmail.com</li>
      <li><svg viewBox="0 0 24 24"><path d="M12 2a10 10 0 1 0 0 20 10 10 0 0 0 0-20zm0 2c.8 1.2 1.5 2.5 1.9 4h-3.8c.4-1.5 1.1-2.8 1.9-4zM4.3 14a8 8 0 0 1 0-4h3.4a16 16 0 0 0 0 4zm5.4 0a14 14 0 0 1 0-4h4.6a14 14 0 0 1 0 4zm6.6 0a16 16 0 0 0 0-4h3.4a8 8 0 0 1 0 4zM12 20c-.8-1.2-1.5-2.5-1.9-4h3.8c-.4 1.5-1.1 2.8-1.9 4z"/></svg>www.yourwebsite.com</li>
    </ul>
    <div class="machine-art" role="img" aria-label="Black silhouette of an excavator arm and bucket"></div>
  </section>

  <section class="card card-back" aria-label="Business card logo side">
    <div class="back-brand"><span class="brand-dot"></span>KLV Plant Services</div>
  </section>
</main>
</body>
</html>
```